business card for a massage therapy practice named 'Cedar and Willow Massage Studio'

I really need a trendy, yet easy on the eyes business card to complement my logo. Ideally with some gold or rose gold foil work.

My uploaded file of the logo I have in horizontal but I have a vertical version as well. Another color that is used in the website is a blush pink here and there. I'd like to see some trendy tropical leaves in the design.

```html
<!DOCTYPE html>
<html lang="en">
<head>
<meta charset="utf-8">
<title>Cedar and Willow Massage Studio – Business Card</title>
<link rel="stylesheet" href="https://fonts.googleapis.com/css2?family=Amatic+SC:wght@700&family=Questrial&display=swap">
<style>
  :root {
    --page-bg: #e9e2d8;
    --card-bg: #f6f3ee;
    --card-edge: #e2dbd0;
    --ink: #4a4744;
    --ink-soft: #5c5955;
    --gold: #9a7a45;
    --leaf-light: #8cc063;
    --leaf-deep: #5e9a3a;
  }
  * { margin: 0; padding: 0; box-sizing: border-box; }
  html, body {
    width: 1200px;
    height: 1047px;
    overflow: hidden;
    background: var(--page-bg);
  }
  .card {
    position: absolute;
    left: 100px;
    top: 250px;
    width: 1000px;
    height: 546px;
    background: var(--card-bg);
    border: 2px solid var(--card-edge);
    border-radius: 22px;
    overflow: hidden;
    box-shadow: 0 18px 40px rgba(80, 64, 40, 0.12);
  }
  .leaf {
    position: absolute;
    background: linear-gradient(135deg, var(--leaf-light), var(--leaf-deep));
    opacity: 0.85;
  }
  .leaf--top-right {
    right: 0;
    top: 0;
    width: 200px;
    height: 190px;
    border-radius: 0 0 0 100% / 0 0 0 100%;
  }
  .leaf--bottom-left {
    left: 0;
    bottom: 0;
    width: 178px;
    height: 190px;
    border-radius: 0 100% 0 0 / 0 100% 0 0;
  }
  .brand {
    position: absolute;
    left: 97px;
    top: 148px;
    display: flex;
    align-items: center;
    gap: 18px;
  }
  .brand__mark {
    width: 46px;
    height: 46px;
    border-radius: 50%;
    background: var(--gold);
    opacity: 0.8;
  }
  .brand__name {
    font-family: "Questrial", sans-serif;
    font-size: 34px;
    line-height: 1.2;
    color: var(--ink);
  }
  .person {
    position: absolute;
    left: 558px;
    top: 158px;
  }
  .person__name {
    font-family: "Amatic SC", cursive;
    font-size: 46px;
    font-weight: 700;
    letter-spacing: 1px;
    color: var(--gold);
    line-height: 1;
  }
  .person__role {
    margin-top: 10px;
    font-family: "Questrial", sans-serif;
    font-size: 22px;
    letter-spacing: 2px;
    color: var(--ink-soft);
  }
  .contact {
    position: absolute;
    left: 558px;
    top: 298px;
    list-style: none;
    font-family: "Questrial", sans-serif;
    font-size: 23px;
    letter-spacing: 0.5px;
    color: var(--ink-soft);
  }
  .contact li { height: 44px; line-height: 44px; }
</style>
</head>
<body>
  <main class="card">
    <div class="leaf leaf--top-right" role="img" aria-label="Tropical palm leaf illustration"></div>
    <div class="leaf leaf--bottom-left" role="img" aria-label="Tropical palm leaf illustration"></div>

    <div class="brand">
      <span class="brand__mark"></span>
      <p class="brand__name">Cedar and Willow<br>Massage Studio</p>
    </div>

    <div class="person">
      <h1 class="person__name">Nora Ellis</h1>
      <p class="person__role">Artist</p>
    </div>

    <ul class="contact">
      <li>Phone: +123 456 789 0</li>
      <li>Email: lorem@ipsum.com</li>
      <li>Web: www.yourwebsite.com</li>
    </ul>
  </main>
</body>
</html>
```